Billboard Velto-Link Systems

Design of an A0 billboard (landscape, will be printed on adhesive foil) of our company with reference to the website (www.velto-link.example) and the activity through keywords / phrases such as Fastest data radio you can buy, data radio safe and independent , ...
Explanation: we set up radio networks for long-range data transmission, which work on our own frequencies and are therefore independent of the provider. The systems are used for water and energy supply systems, sewage systems, environmental measurement networks, ...

Industry/Entity Type

Water-, Energie- Distribution, Abwasser...

Requirements
Must have
• Logo, link on website
Nice to have
• Message
Should not have
• picture of our old product from present web. I will be discontinued shortly. Please use the new one I uploaded here.

```html
<!DOCTYPE html>
<html lang="en">
<head>
<meta charset="utf-8">
<title>Velto-Link Systems – Billboard</title>
<link rel="stylesheet" href="https://fonts.googleapis.com/css2?family=Figtree:wght@500;600;700&family=Roboto+Condensed:wght@300&display=swap">
<style>
  :root {
    --brand-blue: #5b88a0;
    --paper: #ffffff;
    --url-grey: #6f6f6f;
    --frame-grey: #7a7a7a;
    --photo-light: #d3cbc1;
    --photo-mid: #a99e92;
    --photo-dark: #6e645b;
  }
  html, body {
    margin: 0;
    padding: 0;
    width: 1200px;
    height: 848px;
    overflow: hidden;
    background: var(--paper);
  }
  .billboard {
    position: relative;
    width: 1200px;
    height: 848px;
    overflow: hidden;
    background: var(--paper);
    font-family: "Figtree", "Helvetica Neue", Arial, sans-serif;
  }
  .billboard__shapes {
    position: absolute;
    inset: 0;
  }
  .brand {
    position: absolute;
    left: 71px;
    top: 50px;
    color: var(--paper);
    line-height: 1;
  }
  .brand__name {
    display: block;
    font-size: 46px;
    font-weight: 700;
    letter-spacing: 1px;
  }
  .brand__descriptor {
    display: block;
    margin-top: 8px;
    font-size: 13.5px;
    font-weight: 700;
    letter-spacing: 1.6px;
  }
  .headline {
    position: absolute;
    left: 72px;
    top: 268px;
    margin: 0;
    color: var(--brand-blue);
    font-size: 102px;
    font-weight: 600;
    line-height: 118px;
    letter-spacing: 0.5px;
  }
  .headline__line { display: block; }
  .web-link {
    position: absolute;
    left: 71px;
    top: 658px;
    width: 530px;
    height: 78px;
    box-sizing: border-box;
    border: 2px solid var(--frame-grey);
    border-radius: 20px;
    display: flex;
    align-items: center;
    justify-content: center;
    font-family: "Roboto Condensed", "Arial Narrow", sans-serif;
    font-weight: 300;
    font-size: 50px;
    color: var(--url-grey);
  }
</style>
</head>
<body>
  <main class="billboard">
    <svg class="billboard__shapes" width="1200" height="848" viewBox="0 0 1200 848" aria-hidden="false">
      <defs>
        <linearGradient id="siteTones" x1="0" y1="0" x2="1" y2="1">
          <stop offset="0" stop-color="var(--photo-light)"/>
          <stop offset="0.55" stop-color="var(--photo-mid)"/>
          <stop offset="1" stop-color="var(--photo-dark)"/>
        </linearGradient>
      </defs>
      <path class="site-photo" role="img"
            aria-label="Aerial photograph of a wastewater treatment plant with round clarifier basins and walkways, in warm sepia tones"
            d="M340 0 C 700 120, 1050 400, 1200 760 L1200 0 Z"
            fill="url(#siteTones)"/>
      <path class="brand-band" d="M0 0 H1045 C 800 40, 300 130, 0 252 Z"
            fill="var(--brand-blue)" opacity="0.95"/>
    </svg>

    <div class="brand">
      <span class="brand__name">VELTO-LINK</span>
      <span class="brand__descriptor">DATA RADIO SYSTEMS</span>
    </div>

    <h1 class="headline">
      <span class="headline__line">Data Radio;</span>
      <span class="headline__line">Safe &amp;</span>
      <span class="headline__line">Independent</span>
    </h1>

    <div class="web-link">www.velto-link.example</div>
  </main>
</body>
</html>
```